Recto Verso Audiology Business Card

Business card with a beautiful design on the back. On the Recto you need the following data Lindqvist Oren Audiologist Hearing Solutions Hearing Protection Tinnitus Hyperacusis Tel: 0482/37 59 08 Email: On the back, you need something nice like the attached file. The logo "Corra Luna" can be in the center The colors of the Logo can not be changed If possible stay in the same colors as the logo Another solution is to put the logo on the front and have a nice back (A mosaic of small ears, hearing aids or other ..) Thank you _______________________________________________________________ Visit card On the Recto Lindqvist Oren Audiologist Hearing Solutions Hearing Protection Tinnitus Hyperacusis Tel: 0482/37 59 08 Email: You can put the logo " Corra Luna "on the Recto of the Verso The colors of the logo can not be changed. If you put the logo on the back, it must be well integrated. On the Verso I need something in the files. something stylish. It's a visit card for an audiologist. You can get ears of hearing aids if you need. Thanks

Target Market(s)

customers

Contact Information for Business Card

Carte de visite standard ou A6

Font styles to use
Serif
Sans Serif

Colors
33a6d7

Requirements
Must have
• the logo and a stylized background.
Nice to have
• It would be nice to have a back side related to audiology (ears, hearing aids etc.)

```html
<!DOCTYPE html>
<html lang="en">
<head>
<meta charset="utf-8">
<title>Corra Luna – Audiology Business Card</title>
<link href="https://fonts.googleapis.com/css2?family=Ubuntu:wght@400&family=Ubuntu+Condensed&display=swap" rel="stylesheet">
<style>
  :root {
    --bg: #e9e6e2;
    --card: #262626;
    --card-pattern-a: #2a3234;
    --card-pattern-b: #263a3e;
    --teal: #3fb4c6;
    --teal-muted: #3d6e79;
    --text: #f2f2f2;
  }
  * { margin: 0; padding: 0; box-sizing: border-box; }
  html, body {
    width: 1200px; height: 419px; overflow: hidden;
    background: var(--bg);
  }
  .stage {
    width: 1200px; height: 419px;
    display: flex; align-items: center; justify-content: center; gap: 80px;
  }
  .card {
    width: 400px; height: 259px;
    background: var(--card);
    position: relative;
    box-shadow: 0 6px 18px rgba(0,0,0,.25);
  }
  /* front: patterned side with brand name */
  .card-front .pattern {
    position: absolute; inset: 0;
    background: radial-gradient(circle at 50% 50%, var(--card-pattern-b), var(--card-pattern-a) 75%);
  }
  .brand {
    position: absolute; left: 50%; top: 50%;
    transform: translate(-50%, -50%);
    background: var(--card);
    padding: 14px 18px;
    font-family: "Ubuntu Condensed", sans-serif;
    font-size: 24px; line-height: 1.05;
    color: var(--teal);
    text-transform: uppercase;
    letter-spacing: 1px;
  }
  /* back: contact details */
  .card-back { padding: 44px 0 0 48px; color: var(--text); }
  .person-name {
    font-family: "Ubuntu Condensed", sans-serif;
    font-size: 21px; color: var(--teal);
    text-transform: uppercase; letter-spacing: 1px; line-height: 1;
  }
  .person-role {
    font-family: "Ubuntu Condensed", sans-serif;
    font-size: 15px; color: var(--teal-muted);
    margin-bottom: 10px;
  }
  .contact-list { list-style: none; font-family: "Ubuntu", sans-serif; font-size: 12px; }
  .contact-list li { display: flex; align-items: center; gap: 8px; height: 19px; }
  .contact-list svg { width: 11px; height: 11px; fill: var(--teal); flex: none; }
  .services {
    font-family: "Ubuntu", sans-serif; font-size: 12px; line-height: 1.45;
    margin-top: 4px; margin-left: -6px;
  }
</style>
</head>
<body>
<main class="stage">
  <section class="card card-front">
    <div class="pattern" role="img" aria-label="Repeating pattern of small stylised ears with sound waves in teal on dark grey"></div>
    <div class="brand">Medical<br>Center<br>Corra<br>Luna</div>
  </section>

  <section class="card card-back">
    <h1 class="person-name">Lindqvist Oren</h1>
    <p class="person-role">Audiologist Hearing</p>
    <ul class="contact-list">
      <li>
        <svg viewBox="0 0 24 24" aria-hidden="true"><path d="M6.6 10.8a15.5 15.5 0 0 0 6.6 6.6l2.2-2.2c.3-.3.7-.4 1-.2 1.1.4 2.3.6 3.6.6.6 0 1 .4 1 1V20c0 .6-.4 1-1 1A17 17 0 0 1 3 4c0-.6.4-1 1-1h3.5c.6 0 1 .4 1 1 0 1.3.2 2.5.6 3.6.1.3 0 .7-.2 1z"/></svg>
        0482/37 59 08
      </li>
      <li>
        <svg viewBox="0 0 24 24" aria-hidden="true"><path d="M2 5h20v14H2z M3.5 6.5 12 13l8.5-6.5" stroke="#262626" stroke-width="1.6"/></svg>
        hello@corraluna.net
      </li>
      <li>
        <svg viewBox="0 0 24 24" aria-hidden="true"><circle cx="12" cy="12" r="10"/><path d="M8 6c2 1 1 3 3 3s1 3-1 3-2 2-1 4M15 15c1-1 3-1 3 1" stroke="#262626" stroke-width="1.8" fill="none"/></svg>
        www.corraluna.net
      </li>
    </ul>
    <p class="services">Solutions Hearing<br>Protection | Tinnitus | Hyperacusis</p>
  </section>
</main>
</body>
</html>
```